Building Design company needing a letterhead

We need a letter head for our Building Design company to send letters etc. to our clients, consultants, councils etc. We would like to see our logo used and company colours. I have attached our style guide and an example of our current letterheads. Top left we would like our logo, top right we would like the company details and at the footer we would like some sort of image/design etc. that suits our brand. I like the Tarrow Design letterhead attached.

Target Market(s)

Professionals, Councils, Consultants, Mums & Dads

Industry/Entity Type

Architecture

Other font styles liked:
• refer the design style guide

Colors
f37122
000000
1b1b1b

Requirements
Must have
• Must have the minimum of a logo, company details and footer
Nice to have
• An image/design made for the footer that would suite our brand and website at www.corvanplans.com.au. Also it would be nice to include the KMEOT logo somewhere perhaps included in the footer.
Should not have
• Large images in the header. I just want the logo and company details.

```html
<!DOCTYPE html>
<html lang="en">
<head>
<meta charset="utf-8">
<title>Corvan Design Letterhead</title>
<link href="https://fonts.googleapis.com/css2?family=Open+Sans:wght@400;600;700&display=swap" rel="stylesheet">
<style>
  :root {
    --backdrop: #5c4b42;
    --paper: #ffffff;
    --brand-orange: #e55a26;
    --ink: #1b1b1b;
    --grey-dark: #6d6e71;
    --grey-light: #b8b8b8;
    --footer-text: #ffffff;
  }
  html, body {
    margin: 0;
    padding: 0;
    width: 967px;
    height: 1200px;
    overflow: hidden;
    background: var(--backdrop);
    font-family: "Open Sans", sans-serif;
  }
  .letterhead {
    position: absolute;
    left: 135px;
    top: 133px;
    width: 720px;
    height: 932px;
    background: var(--paper);
    box-shadow: 2px 3px 6px rgba(0,0,0,0.35);
    overflow: hidden;
  }
  .brand {
    position: absolute;
    left: 52px;
    top: 44px;
    display: flex;
    align-items: center;
    gap: 22px;
  }
  .brand-square {
    width: 64px;
    height: 64px;
    background: var(--brand-orange);
  }
  .brand-name {
    font-weight: 700;
    font-size: 38px;
    line-height: 40px;
    letter-spacing: 2px;
    color: var(--ink);
    text-transform: uppercase;
  }
  .affiliation {
    position: absolute;
    left: 584px;
    top: 38px;
    width: 62px;
    text-align: center;
  }
  .affiliation-square {
    width: 56px;
    height: 56px;
    border: 3px solid var(--brand-orange);
  }
  .affiliation-name {
    margin-top: 4px;
    font-size: 15px;
    font-weight: 400;
    color: var(--brand-orange);
    letter-spacing: 0.5px;
  }
  .footer-art {
    position: absolute;
    left: 0;
    top: 0;
  }
  .contact {
    position: absolute;
    top: 886px;
    color: var(--footer-text);
    font-size: 11px;
    line-height: 16px;
    margin: 0;
  }
  .contact-address { left: 40px; }
  .contact-phone { left: 286px; }
  .contact-web { left: 486px; top: 884px; }
  .contact-web .abn { font-size: 8px; line-height: 10px; display: block; }
  .contact-web .url { font-size: 13.5px; font-weight: 600; line-height: 22px; display: block; letter-spacing: 0.3px; }
  .divider {
    position: absolute;
    top: 889px;
    width: 1px;
    height: 26px;
    background: #f3906a;
  }
  .divider-one { left: 264px; }
  .divider-two { left: 454px; }
</style>
</head>
<body>
  <main class="letterhead">
    <header>
      <div class="brand">
        <div class="brand-square"></div>
        <div class="brand-name">Corvan<br>Design</div>
      </div>
      <div class="affiliation">
        <div class="affiliation-square"></div>
        <div class="affiliation-name">KMEOT</div>
      </div>
    </header>

    <svg class="footer-art" width="720" height="932" viewBox="0 0 720 932" aria-hidden="true">
      <path d="M0,838 Q300,832 560,850" fill="none" stroke="var(--grey-light)" stroke-width="3"/>
      <path d="M0,845 Q380,838 720,888 L720,897 Q380,850 0,855 Z" fill="var(--grey-dark)"/>
      <path d="M0,862 Q380,858 720,900 L720,932 L0,932 Z" fill="var(--brand-orange)"/>
    </svg>

    <footer>
      <p class="contact contact-address">Unit 3/22 Harlow Way Westbrook WA 6999<br>PO Box 5180 Westbrook North WA 6999</p>
      <span class="divider divider-one"></span>
      <p class="contact contact-phone">Ph: (08) 5550 1234<br>admin@corvanplans.com.au</p>
      <span class="divider divider-two"></span>
      <p class="contact contact-web"><span class="abn">ABN 11 222 333 444</span><span class="url">www.corvanplans.com.au</span></p>
    </footer>
  </main>
</body>
</html>
```